Electronics Recycling and IT Asset Disposition Flyer and Brochure Design

We need a 2 side A5 Flyer and 4 side A4 folder( brochure) for our electronics waste recycling and IT asset management and disposition business.
Our business provides free electronics waste recycling for companies, schools, learning institutions,councils, IT companies and government sectors. Many people are ignorant of responsible recycling of electronics which could harm our health if not treated properly.
The list of other services attached in the pdf.
We provide an end to end and tailored solution for our customers from collection, logistics, data sanitisation, remarketing and recycling.

The Flyer should create awareness of responsible electronics recycling and drive the audience to contact us or go to our website to learn more about the company and services.A brief list of services should also be included in the flyer.The goal is to get the audience to contact us to enquire more about our services.

The Brochure should include all the above plus provide more details about the company, processes, services,contact details (fb, linkedin,Twitter). The goal is to convert the audience to customers for recycling and provide other services as added services.

The final design for both flyer and brochure should communicate responsible recycling of electronic scrap and tailored solution for every organisation.

The company website is www.kelvane-scrap.com.au based in Australia. We serve clients nationwide.

Target Market(s)

IT companies, Corporate, schools and learning institutions, government sector

Industry/Entity Type

Recycling

Contact Information for Business Card

Name: Harold Pendrake
email: harold@kelvane-scrap.com.au
website: www.kelvane-scrap.com.au
mobile: +614 612 39057
Phone: 1300 46 2735

Font styles to use
Serif

Requirements
Must have
• I would like the designs to have more images and icons
Nice to have
Should not have
• none

```html
<!DOCTYPE html>
<html lang="en">
<head>
<meta charset="utf-8">
<title>Kelvane Scrap – Brochure Spread</title>
<link href="https://fonts.googleapis.com/css2?family=Nunito:wght@400;600;700;800&display=swap" rel="stylesheet">
<style>
:root{
  --green:#6ab043;
  --green-dark:#1f7a3c;
  --green-deep:#0f4a25;
  --grey:#6d6e70;
  --grey-dark:#58595b;
  --band:#efefef;
  --ink:#3a3a3a;
  --paper:#ffffff;
  --bg:#ececec;
}
*{margin:0;padding:0;box-sizing:border-box}
html,body{width:1200px;height:904px;overflow:hidden;background:var(--bg)}
body{font-family:"Nunito",sans-serif;color:var(--ink)}
.canvas{position:relative;width:1200px;height:904px}
.page{position:absolute;top:60px;width:561px;height:790px;background:var(--paper);overflow:hidden}
.page--left{left:36px}
.page--right{left:597px;border-left:1px solid #d8d8d8}
.brand-badge{position:absolute;width:82px;height:82px;border-radius:50%;background:var(--paper);border:2px solid var(--green);display:flex;align-items:center;justify-content:center;text-align:center;z-index:3}
.brand-badge span{font-weight:800;color:var(--green-dark);font-size:12px;line-height:1.1}
.hero-photo{position:absolute;left:0;top:70px;width:561px;height:128px;background:linear-gradient(135deg,#3f4a3d,#7d8a76 45%,#c9cfc5)}
.section-title{position:absolute;color:var(--green);font-weight:600;font-size:29px;text-align:center;width:100%}
.about-band{position:absolute;left:0;top:238px;width:561px;height:212px;background:var(--green);color:#fff;padding:13px 52px 0 89px;font-size:8.6px;line-height:1.2}
.about-band p{margin-bottom:10px}
.laptop-photo{position:absolute;left:0;top:450px;width:561px;height:330px;background:linear-gradient(160deg,#fbfbfb,#e9e9e9 60%,#f5f5f5)}
.cycle{position:absolute;left:164px;top:500px}
.cycle-label{position:absolute;font-weight:800;font-size:9px}
.cycle-num{position:absolute;font-weight:800;font-size:36px;line-height:1}
.cycle-text{position:absolute;font-size:4.6px;line-height:1.25}
.cycle-core{position:absolute;left:233px;top:597px;width:120px;text-align:center;font-weight:700;font-size:16px;line-height:1.25;color:var(--ink)}
.folio{position:absolute;top:741px;display:flex;align-items:center;gap:6px;font-size:10.5px}
.folio b{display:inline-block;width:18px;height:18px;background:var(--green);color:#fff;font-weight:400;font-size:9px;text-align:center;line-height:18px}
.folio i{width:1px;height:16px;background:var(--ink)}
.foot-strip{position:absolute;bottom:0;height:10px;display:flex;width:100%}
.foot-strip span{height:100%}
.rule{position:absolute;left:0;top:71px;width:561px;height:1px;background:var(--green)}
.service{position:absolute;left:0;width:561px}
.service--band{background:var(--band)}
.service-icon{position:absolute;left:70px;width:36px;height:36px;border-radius:50%;background:#fff;border:2px solid var(--green);display:flex;align-items:center;justify-content:center}
.service-body{position:absolute;left:138px;right:30px;font-size:7.6px;line-height:1.12}
.service-body h3{color:var(--green);font-size:10.5px;font-weight:800;margin-bottom:1px}
.industries{position:absolute;left:0;top:535px;width:561px;height:255px;background:var(--band)}
.industries h3{position:absolute;top:40px;width:100%;text-align:center;color:var(--green-dark);font-size:11.5px;font-weight:800}
.industries p{position:absolute;left:56px;right:50px;top:63px;text-align:center;font-size:7.8px;line-height:1.2}
.industries .lead{position:absolute;left:170px;top:108px;font-size:7.8px}
.industries ul{position:absolute;left:156px;top:122px;list-style:none;font-size:7.8px;line-height:1.17}
.industries li::before{content:"";display:inline-block;width:4px;height:4px;background:var(--green);margin-right:10px;vertical-align:1px}
</style>
</head>
<body>
<div class="canvas">

  <section class="page page--left">
    <div class="hero-photo" role="img" aria-label="Close-up photograph of a green electronic circuit board with chips"></div>
    <div class="brand-badge" style="left:245px;top:7px"><span>Kelvane<br>Scrap</span></div>
    <h1 class="section-title" style="top:198px;left:-6px">About Us</h1>
    <div class="about-band">
      <p>Kelvane Scrap is a full service IT asset disposition, electronics waste recycling and electronics scrap purchasing company in Australia. Our vision is to become an industry leader by building genuine relationships with clients based on integrity, service quality and consistency, as well as maximizing value recovery.</p>
      <p>Our focus is to reduce electronic waste generation through creating awareness in organisations and community about the importance of responsible recycling of electronics waste. Our goal is to provide end-to-end solution in e-waste management through established processes and technological innovations, drive higher returns for our customers and enhance conservation of raw metals within our ecosystem.</p>
      <p>Our team of dedicated engineers and professionals work with companies, government offices, institutions and SMEs across Australia to provide personalised IT asset disposal and e-waste management solutions to suit their needs. Our experience and knowledge in this industry will help us to understand and provide innovative solutions to manage your end of life IT assets. We aim at maximising returns and providing cost effective ways to ensure a positive impact on your bottom-line.</p>
    </div>
    <div class="laptop-photo" role="img" aria-label="Faint photograph of hands typing on a laptop keyboard"></div>
    <h2 class="section-title" style="top:455px;left:-10px">E-waste Recycling</h2>

    <svg class="cycle" width="260" height="260" viewBox="0 0 260 260" aria-hidden="true">
      <path d="M5 130 A125 125 0 0 1 192.5 21.75 L161 76.3 A62 62 0 0 0 68 130 Z" fill="var(--green)"/>
      <path d="M192.5 21.75 A125 125 0 0 1 225.75 210.4 L177.5 169.9 A62 62 0 0 0 161 76.3 Z" fill="#fff" stroke="#c9d9b8" stroke-width="1"/>
      <path d="M225.75 210.4 A125 125 0 0 1 5 130 L68 130 A62 62 0 0 0 177.5 169.9 Z" fill="var(--grey)"/>
      <circle cx="130" cy="130" r="58" fill="#fff" stroke="#e2e2e2" stroke-width="3"/>
      <g fill="none" stroke="#fff" stroke-width="2.4" stroke-linecap="round">
        <path d="M66 30 a7 7 0 1 1 -6 4"/><path d="M57 31 l3 3 l3 -3"/>
      </g>
      <g stroke="var(--grey-dark)" stroke-width="3" stroke-linecap="round">
        <line x1="188" y1="37" x2="206" y2="55"/><line x1="206" y1="37" x2="188" y2="55"/>
      </g>
      <g fill="none" stroke="#fff" stroke-width="2" stroke-linecap="round">
        <path d="M192 215 l7 -11 l7 11 z"/>
      </g>
    </svg>
    <span class="cycle-num" style="left:251px;top:515px;color:#fff">01</span>
    <span class="cycle-label" style="left:196px;top:555px;color:#fff">REUSE</span>
    <span class="cycle-text" style="left:183px;top:568px;width:52px;color:#fff">Reuse: The first step of the process is to check each device and identify its usability and function to set its value. Working units are kept for reuse.</span>
    <span class="cycle-label" style="left:341px;top:571px;color:var(--grey)">RECOVER</span>
    <span class="cycle-text" style="left:359px;top:586px;width:56px;color:var(--ink)">Recover: The device that does not pass the initial visual inspection will be segregated and sorted for dismantling process.</span>
    <span class="cycle-num" style="left:363px;top:648px;color:var(--grey-dark)">02</span>
    <span class="cycle-num" style="left:188px;top:676px;color:#fff">03</span>
    <span class="cycle-label" style="left:241px;top:698px;color:#fff">RECYCLE</span>
    <span class="cycle-text" style="left:241px;top:711px;width:66px;color:#fff">Recycle: All the dismantled components and materials are then sent to refineries for further refining and used as raw material for new products</span>
    <div class="cycle-core">E-waste<br>Recycling</div>

    <div class="folio" style="left:46px"><b>01</b><i></i><span>About Us</span></div>
    <div class="foot-strip"><span style="width:46px;background:var(--green)"></span><span style="width:72px;background:var(--green-dark)"></span><span style="width:82px;background:var(--green-deep)"></span><span style="flex:1;background:#cfcfcf"></span></div>
  </section>

  <section class="page page--right">
    <div class="brand-badge" style="left:230px;top:7px"><span>Kelvane<br>Scrap</span></div>
    <div class="rule"></div>
    <h1 class="section-title" style="top:108px;left:-3px">Service Offering</h1>

    <div class="service" style="top:177px;height:21px">
      <div class="service-body" style="top:2px"><h3>Secure E-Waste Collection Service</h3></div>
    </div>
    <div class="service service--band" style="top:198px;height:42px">
      <div class="service-icon" style="top:3px"><svg width="20" height="20" viewBox="0 0 20 20" fill="none" stroke="var(--green)" stroke-width="2"><path d="M10 3 l5 8 h-10 z"/><path d="M4 15 h12"/></svg></div>
      <div class="service-body" style="top:4px">Kelvane Scrap collects electronic waste from schools, businesses, home users and government departments<br>Secure collection includes pick up of e-waste and transportation to our recycling facility in a<br>secured truck<br>Registration of assets and reporting</div>
    </div>
    <div class="service" style="top:250px;height:50px">
      <div class="service-icon" style="top:8px"><svg width="18" height="18" viewBox="0 0 18 18" fill="none" stroke="var(--green)" stroke-width="1.6"><rect x="3" y="2" width="12" height="14"/><path d="M6 6h6M6 9h6M6 12h4"/></svg></div>
      <div class="service-body" style="top:5px"><h3>Certified Data Sanitisation Service</h3>Registering your assets on our Asset Management System<br>Test, audit and verify specifications, condition and resale value Provide a detailed asset report<br>Cleaning and removal of company logos and asset tags</div>
    </div>
    <div class="service service--band" style="top:307px;height:80px">
      <div class="service-icon" style="top:20px"><svg width="18" height="18" viewBox="0 0 18 18" fill="none" stroke="var(--green)" stroke-width="1.6"><ellipse cx="9" cy="5" rx="6" ry="2.5"/><path d="M3 5v8c0 1.4 2.7 2.5 6 2.5s6-1.1 6-2.5V5"/></svg></div>
      <div class="service-body" style="top:6px"><h3>Certified Data Erasure Services</h3>To provide secure data destruction:<br>X1 pass<br>X3 pass (Recommended, Fedline standard)<br>X7 pass<br>Total destruction of HDDs by degaussing<br>Total physical destruction of any storage media by shredding</div>
    </div>
    <div class="service" style="top:390px;height:36px">
      <div class="service-icon" style="top:0"><svg width="18" height="18" viewBox="0 0 18 18" fill="none" stroke="var(--green)" stroke-width="1.8" stroke-linecap="round"><path d="M14 6a6 6 0 0 0-11 2"/><path d="M4 12a6 6 0 0 0 11-2"/></svg></div>
      <div class="service-body" style="top:5px"><h3>IT Asset Remarketing</h3>Recover client's IT asset and mobile devices for valuation and remarketing</div>
    </div>
    <div class="service service--band" style="top:428px;height:44px">
      <div class="service-icon" style="top:4px"><svg width="18" height="18" viewBox="0 0 18 18" stroke="var(--green)" stroke-width="2.4" stroke-linecap="round"><line x1="3" y1="3" x2="15" y2="15"/><line x1="15" y1="3" x2="3" y2="15"/></svg></div>
      <div class="service-body" style="top:2px"><h3>Ewaste Recycling</h3>All assets with no market value will be processed as E-Waste and recycled with zero to landfill<br>in our ISO certified partner refinery overseas for metals recovery</div>
    </div>
    <div class="service" style="top:476px;height:50px">
      <div class="service-icon" style="top:5px"><svg width="18" height="18" viewBox="0 0 18 18" fill="none" stroke="var(--green)" stroke-width="1.8"><circle cx="9" cy="9" r="6"/><path d="M7.5 6.5 l4 2.5 l-4 2.5 z" fill="var(--green)"/></svg></div>
      <div class="service-body" style="top:2px"><h3>Logistics Solutions</h3>Deployment, relocation and decommissioning of IT systems by professional Norvex and Taltrix<br>certified engineers<br>Data Center decommissioning/racking/de-racking and relocation<br>IT Systems deployment and support for small and medium size business</div>
    </div>

    <div class="industries">
      <div class="service-icon" style="left:293px;top:6px;width:34px;height:34px"><svg width="16" height="16" viewBox="0 0 16 16" fill="none" stroke="var(--green)" stroke-width="1.6"><rect x="2" y="5" width="12" height="9"/><path d="M5 5V2h6v3"/></svg></div>
      <h3>Industries Served</h3>
      <p>No matter how big or small your organisation is or how complex or simple your IT systems are, we listen to the needs of your organisation to deliver customized, cost-effective and scalable solution. We ensure data destruction and responsible recycling of your electronic assets are our utmost priority. Our dedicated team is ready to serve you.</p>
      <span class="lead">Industries we serve:</span>
      <ul>
        <li>Corporate</li>
        <li>ITAD Companies</li>
        <li>Financial Institutions</li>
        <li>Educational &amp; Learning Institutions</li>
        <li>Councils</li>
        <li>Recycling companies</li>
        <li>Government sector</li>
      </ul>
    </div>

    <div class="folio" style="left:46px;top:743px"><b>01</b><i></i><span>Service Offering</span></div>
    <div class="foot-strip"><span style="flex:1;background:#cfcfcf"></span><span style="width:82px;background:var(--green-deep)"></span><span style="width:72px;background:var(--green-dark)"></span><span style="width:46px;background:var(--green)"></span></div>
  </section>

</div>
</body>
</html>
```